Animal Eye Clinic needs a Business card

We are a new veterinary ophthalmology practice (Ridgeline Pet Vision Care) and we need a business card designed. We only see animal eyes - we are not a regular veterinary clinic. We already have a logo. We are looking for a professional, good looking business card to hand out to our clients. We are looking for something simple but professional and contemporary. Our logo is likely the only picture/graphic that needs to be on the card.
Updates

Contact Information for Business Card

Delia Vossman, BSc, DVM, MSc, DipACVO
Veterinary Ophthalmologist

Phone: 250.418.3927
Email: ridgelinepetvisioncare@mailbox-example.net
Website: ridgelinepetvisioncare-example.net
Address: 1874 Thornbury Rd
Kelowna, BC, V1X 4M9

Colors

Designer to choose colors to be used in the design.

Requirements
Must have
• Our logo (attached)

```html
<!DOCTYPE html>
<html lang="en">
<head>
<meta charset="utf-8">
<title>Ridgeline Pet Vision Care – Business Card</title>
<link rel="stylesheet" href="https://fonts.googleapis.com/css2?family=Roboto:wght@400;500;700&display=swap">
<style>
  :root {
    --page-bg: #d8d1c6;
    --card-top: #f4f6f7;
    --card-bottom: #e6eaec;
    --card-edge: #c9ced1;
    --teal: #1f7a80;
    --ink: #474a4c;
    --rule: #4a4d4f;
  }
  * { margin: 0; padding: 0; box-sizing: border-box; }
  html, body {
    width: 1200px;
    height: 976px;
    overflow: hidden;
    background: var(--page-bg);
    font-family: "Roboto", Arial, sans-serif;
  }
  .card {
    position: absolute;
    left: 60px;
    top: 189px;
    width: 1080px;
    height: 598px;
    border-radius: 26px;
    border: 1px solid var(--card-edge);
    background: linear-gradient(160deg, var(--card-top), var(--card-bottom));
    box-shadow: 0 18px 40px rgba(60, 50, 40, 0.18);
    overflow: hidden;
  }
  .brand {
    position: absolute;
    left: 58px;
    top: 70px;
    display: flex;
    align-items: center;
    gap: 34px;
  }
  .brand-mark {
    width: 92px;
    height: 92px;
    border-radius: 50%;
    background: var(--teal);
  }
  .brand-name {
    font-size: 42px;
    font-weight: 700;
    color: var(--teal);
    letter-spacing: 0.2px;
  }
  .person {
    position: absolute;
    left: 230px;
    top: 282px;
  }
  .person-name {
    font-size: 31px;
    font-weight: 500;
    color: var(--teal);
    line-height: 1.1;
  }
  .person-title {
    font-size: 25px;
    color: var(--ink);
    line-height: 1.2;
    margin-top: 2px;
  }
  .divider {
    position: absolute;
    left: 230px;
    right: 0;
    top: 357px;
    height: 2px;
    background: var(--rule);
  }
  .address {
    position: absolute;
    left: 230px;
    top: 376px;
    font-size: 25px;
    line-height: 31px;
    color: var(--ink);
    font-style: normal;
  }
  .contacts {
    position: absolute;
    left: 230px;
    top: 457px;
    list-style: none;
    font-size: 26px;
    color: var(--ink);
  }
  .contacts li {
    display: flex;
    align-items: center;
    gap: 10px;
    height: 33px;
  }
  .contacts svg {
    width: 21px;
    height: 21px;
    fill: var(--teal);
    flex: none;
  }
</style>
</head>
<body>
  <section class="card">
    <div class="brand">
      <span class="brand-mark"></span>
      <span class="brand-name">Ridgeline Pet Vision Care</span>
    </div>

    <div class="person">
      <p class="person-name">Delia Vossman, BSc, DVM, MSc, DipACVO</p>
      <p class="person-title">Veterinary Ophthalmologist</p>
    </div>

    <div class="divider"></div>

    <address class="address">
      1874 Thornbury Rd<br>
      Kelowna, BC, V1X 4M9
    </address>

    <ul class="contacts">
      <li>
        <svg viewBox="0 0 24 24" aria-hidden="true"><path d="M6.6 10.8a15.1 15.1 0 0 0 6.6 6.6l2.2-2.2a1 1 0 0 1 1-.25 11.4 11.4 0 0 0 3.6.57 1 1 0 0 1 1 1V20a1 1 0 0 1-1 1A17 17 0 0 1 3 4a1 1 0 0 1 1-1h3.5a1 1 0 0 1 1 1c0 1.25.2 2.45.57 3.6a1 1 0 0 1-.25 1z"/></svg>
        <span>250.418.3927</span>
      </li>
      <li>
        <svg viewBox="0 0 24 24" aria-hidden="true"><path d="M2 5h20v14H2z M3.5 6.5 12 13l8.5-6.5v11h-17z" fill-rule="evenodd"/></svg>
        <span>ridgelinepetvisioncare@mailbox-example.net</span>
      </li>
      <li>
        <svg viewBox="0 0 24 24" aria-hidden="true"><path fill-rule="evenodd" d="M12 2a10 10 0 1 0 0 20 10 10 0 0 0 0-20zm-1 2.1V8H7.6A8 8 0 0 1 11 4.1zm2 0A8 8 0 0 1 16.4 8H13zM6.6 10H11v4H6.6a8 8 0 0 1 0-4zm6.4 0h4.4a8 8 0 0 1 0 4H13zm-5.4 6H11v3.9A8 8 0 0 1 7.6 16zm5.4 0h3.4a8 8 0 0 1-3.4 3.9z"/></svg>
        <span>ridgelinepetvisioncare-example.net</span>
      </li>
    </ul>
  </section>
</body>
</html>
```